Private Investment Firm Needs PowerPoint Presentation Template

Design PowerPoint template, take Pinebrook-submitted rough presentation draft, and drop it into new template. See attached Project Brief file for more detail.
Updates

Some decent designs have been submitted but they seem to lack the understanding of our target markets. I am hopeful that more time and feedback will result in better results.

Target Market(s)

Private company owners and intermediaries.

Font styles to use
Serif

Colors
3176b5

Requirements
Must have
• See attached Project Brief.
Nice to have
Should not have
• No B2C fluff--this is a B2B project.

```html
<!DOCTYPE html>
<html lang="en">
<head>
<meta charset="utf-8">
<title>Introduction – Pinebrook Capital</title>
<link href="https://fonts.googleapis.com/css2?family=Nunito+Sans:wght@400;700&family=Tinos&display=swap" rel="stylesheet">
<style>
  :root {
    --brand-blue: #0f6cc2;
    --ink: #1b1b1b;
    --paper: #ffffff;
    --photo-top: #9fd3d6;
    --photo-mid: #6f7d80;
    --photo-bottom: #3a4346;
  }
  * { margin: 0; padding: 0; box-sizing: border-box; }
  html, body { width: 1200px; height: 676px; overflow: hidden; background: var(--paper); }
  .slide { position: relative; width: 1200px; height: 676px; background: var(--paper); font-family: "Nunito Sans", sans-serif; color: var(--ink); }
  .side-band { position: absolute; left: 0; top: 0; width: 44px; height: 676px; background: var(--brand-blue); }
  .side-url {
    position: absolute; left: 22px; top: 336px;
    transform: translate(-50%, -50%) rotate(-90deg);
    font-family: "Tinos", serif; font-size: 16px; color: var(--paper); white-space: nowrap; letter-spacing: 0.2px;
  }
  .right-band { position: absolute; left: 976px; top: 0; width: 224px; height: 676px; background: var(--brand-blue); }
  .page-number { position: absolute; right: 30px; top: 18px; font-family: "Tinos", serif; font-size: 19px; color: var(--ink); }
  .city-photo {
    position: absolute; left: 793px; top: 78px; width: 347px; height: 520px;
    background: linear-gradient(180deg, var(--photo-top) 0%, var(--photo-mid) 45%, var(--photo-bottom) 100%);
  }
  .title { position: absolute; left: 86px; top: 78px; font-size: 30px; font-weight: 700; color: var(--brand-blue); letter-spacing: 0.8px; }
  .points { position: absolute; left: 86px; top: 143px; width: 670px; list-style: none; font-size: 17.2px; line-height: 28px; letter-spacing: 0.2px; }
  .points li { position: relative; padding-left: 28px; }
  .points li::before {
    content: ""; position: absolute; left: 1px; top: 7px; width: 13px; height: 13px; background: var(--brand-blue);
  }
  .points .sub { list-style: none; }
  .points .sub li { padding-left: 23px; }
  .brand { position: absolute; left: 67px; top: 612px; display: flex; align-items: center; gap: 10px; }
  .brand-dot { width: 34px; height: 34px; border-radius: 50%; background: var(--brand-blue); }
  .brand-name { font-family: "Nunito Sans", sans-serif; font-weight: 700; font-size: 18px; color: var(--brand-blue); letter-spacing: 1px; }
</style>
</head>
<body>
  <div class="slide">
    <div class="side-band"></div>
    <div class="side-url">www.pinebrookcapital.com</div>
    <div class="right-band"></div>
    <div class="page-number">1</div>
    <div class="city-photo" role="img" aria-label="Photograph of a downtown city street lined with tall office towers"></div>

    <h1 class="title">INTRODUCTION</h1>
    <ul class="points">
      <li>Private company owners have traditionally considered two capital raising options:
        <ul class="sub">
          <li>Borrow from a local bank, or</li>
          <li>Sell most or all of the company to a change-of-control investor (aka Buyout firm)</li>
        </ul>
      </li>
      <li>An alternative most have not considered is the raising of Non-Control Capital, or capital that is invested into the business yet allows those same owners to retain controlling interest in their company</li>
      <li>Non-Control Capital is not appropriate for every private company owner but neither is a Change-of-Control sale</li>
      <li>The key is to determine what the business and owners require, and then partner with an investor best aligned with those needs so that long-term company growth, and personal goals, can both be achieved</li>
    </ul>

    <div class="brand">
      <div class="brand-dot"></div>
      <div class="brand-name">PINEBROOK CAPITAL</div>
    </div>
  </div>
</body>
</html>
```